Medical Practice needs a Letterhead Design

We need a clean, modern letterhead design for our stem cell medical practice.

Industry/Entity Type

Medical

```html
<!DOCTYPE html>
<html lang="en">
<head>
<meta charset="utf-8">
<title>VitaCore Clinic Letterhead</title>
<link href="https://fonts.googleapis.com/css2?family=Carlito:ital,wght@0,400;0,700;1,400&display=swap" rel="stylesheet">
<style>
  :root {
    --backdrop: #e6e6e6;
    --paper: #ffffff;
    --ink: #1f1f1f;
    --navy: #12334a;
    --lime: #b3c43a;
    --muted: #55606a;
  }
  html, body {
    margin: 0;
    width: 1200px;
    height: 1000px;
    overflow: hidden;
    background: var(--backdrop);
  }
  .letterhead {
    position: absolute;
    left: 252px;
    top: 50px;
    width: 696px;
    height: 900px;
    background: var(--paper);
    box-shadow: 0 2px 10px rgba(0,0,0,0.18);
    font-family: "Carlito", sans-serif;
    color: var(--ink);
  }
  .brand {
    position: absolute;
    right: 52px;
    top: 70px;
    display: flex;
    align-items: center;
    gap: 8px;
    font-size: 30px;
    font-weight: 700;
    color: var(--navy);
    letter-spacing: 0.2px;
  }
  .brand-dot {
    width: 12px;
    height: 12px;
    border-radius: 50%;
    background: var(--lime);
  }
  .letter {
    position: absolute;
    left: 56px;
    right: 56px;
    top: 150px;
    font-size: 11.5px;
    line-height: 1.75;
  }
  .letter p { margin: 0 0 22px; }
  .salutation { margin-bottom: 26px !important; }
  .closing { margin: 0 0 8px !important; }
  .signature {
    width: 150px;
    height: 46px;
    background: linear-gradient(90deg, #d9d9d9, #c4c4c4);
    border-radius: 4px;
    margin-bottom: 10px;
  }
  .footer {
    position: absolute;
    left: 56px;
    right: 40px;
    bottom: 60px;
    font-size: 9px;
    color: var(--muted);
    line-height: 1.6;
  }
  .footer b { color: var(--navy); font-weight: 700; }
  .footer .row { display: flex; gap: 22px; }
  .footer .address { color: var(--navy); font-weight: 700; }
  .band {
    position: absolute;
    left: 0;
    right: 0;
    bottom: 28px;
    height: 26px;
    display: flex;
  }
  .band-navy { flex: 3; background: var(--navy); }
  .band-lime { flex: 1; background: var(--lime); }
</style>
</head>
<body>
<div class="letterhead">
  <div class="brand"><span class="brand-dot"></span>VitaCore Clinic</div>

  <div class="letter">
    <p class="salutation">Lorem Ipsum is simply</p>
    <p>dummy text of the printing and typesetting industry. Lorem Ipsum has been the industry's standard dummy text ever since the 1500s, when an unknown printer took a galley of type and scrambled it to make a type specimen book. It has survived not only five centuries, but also the leap into electronic typesetting, remaining essentially unchanged. It was popularised in the 1960s with the release of Typerail sheets containing Lorem Ipsum passages, and more recently with desktop publishing software like Quillset Composer including versions of Lorem Ipsum.</p>
    <p>It is a long established fact that a reader will be distracted by the readable content of a page when looking at its layout. The point of using Lorem Ipsum is that it has a more-or-less normal distribution of letters, as opposed to using 'Content here, content here', making it look like readable English. Many desktop publishing packages and web page editors now use Lorem Ipsum as their default model text, and a search for 'lorem ipsum' will uncover many web sites still in their infancy. Various versions have evolved over the years, sometimes by accident, sometimes on purpose (injected humour and the like).</p>
    <p>Contrary to popular belief, Lorem Ipsum is not simply random text. It has roots in a piece of classical Latin literature from 45 BC, making it over 2000 years old. Daniel Hartwell, a Latin professor at Ashford College</p>
    <p class="closing">Lorem Ipsum</p>
    <div class="signature" role="img" aria-label="Handwritten signature"></div>
    <p>Lorem Ipsum is a dummy</p>
  </div>

  <div class="footer">
    <div class="row">
      <span><b>P:</b> (000)412-3380</span>
      <span><b>F:</b> (000)412-3391</span>
      <span><b>E:</b> hello@vitacoreclinic.com</span>
      <span><b>W:</b> www.vitacoreclinic.com</span>
    </div>
    <div class="address">480 Linden Avenue, Suite 210, Fairmont, OR 97405</div>
  </div>

  <div class="band">
    <div class="band-navy"></div>
    <div class="band-lime"></div>
  </div>
</div>
</body>
</html>
```